Re-Design of a 1 Pager IT Security Website

Please create a 1 Pager design for this website and all its elements: http://www.quillstonebrightmarsh.com/

Colours, Fonts etc: You can select whatever you prefer

```html
<!DOCTYPE html>
<html lang="en">
<head>
<meta charset="utf-8">
<title>Domain Monitoring</title>
<link rel="stylesheet" href="https://fonts.googleapis.com/css2?family=Kanit:wght@400;500;600&family=Catamaran:wght@400;500;600&display=swap">
<style>
:root{
  --bg-deep:#12020f;
  --bg-about:#1a0417;
  --bg-panel:#22061f;
  --bg-card:#2e0b2c;
  --bg-footer:#17031a;
  --pink:#ff1670;
  --orange:#ffa35a;
  --text:#ffffff;
  --muted:#e6d9e4;
  --ghost:rgba(255,255,255,0.05);
  --line:#5a3a55;
}
*{margin:0;padding:0;box-sizing:border-box}
html,body{width:1200px;height:3829px;overflow:hidden}
body{background:var(--bg-deep);color:var(--text);font-family:'Catamaran',sans-serif;position:relative}
h1,h2,h3,.brand,.btn{font-family:'Kanit',sans-serif;font-weight:500}
.abs{position:absolute}
.btn{position:absolute;display:inline-block;color:#fff;font-size:19px;padding:10px 20px;border-radius:12px 12px 12px 12px;
  background:linear-gradient(90deg,var(--pink),var(--orange));box-shadow:5px 5px 0 -1px #1b0414,6px 6px 0 0 #b0704a;text-decoration:none}
/* nav */
.nav{position:absolute;top:0;left:0;width:1200px;height:110px;z-index:3}
.brand{position:absolute;top:38px;left:110px;font-size:26px;color:#fff}
.nav-links{position:absolute;top:46px;left:425px;display:flex;gap:0;font-family:'Kanit',sans-serif;font-size:14.5px}
.nav-links a{color:#fff;text-decoration:none;margin-right:44px}
.nav-links a.active{color:var(--orange);text-decoration:underline}
.nav .btn{top:34px;left:972px;font-size:15px;padding:6px 18px}
/* hero */
.hero{position:absolute;top:0;left:0;width:1200px;height:655px;background:var(--bg-deep);overflow:hidden}
.hero-art{position:absolute;top:0;left:360px;width:840px;height:655px;
  background:radial-gradient(ellipse 55% 55% at 62% 38%,#c8105a 0%,#7a0a3e 40%,rgba(30,2,20,0) 75%)}
.hero h1{position:absolute;top:220px;left:110px;font-size:52px;line-height:62px;font-weight:500}
.hero .lead{position:absolute;top:358px;left:110px;font-size:20px;color:var(--muted)}
.hero .btn{top:418px;left:112px}
/* section shared */
.ghost{position:absolute;left:0;width:1200px;text-align:center;font-family:'Kanit',sans-serif;font-weight:600;color:var(--ghost);font-size:96px;letter-spacing:2px;line-height:1}
.sec-title{position:absolute;left:0;width:1200px;text-align:center;font-size:32px}
.sec-text{position:absolute;text-align:center;font-size:17.5px;line-height:34px;color:var(--muted)}
.about{position:absolute;top:655px;left:0;width:1200px;height:532px;background:var(--bg-about)}
.risk{position:absolute;top:1187px;left:0;width:1200px;height:850px;background:var(--bg-panel)}
.card{position:absolute;top:481px;width:292px;height:278px;background:var(--bg-card);border-radius:22px;text-align:center}
.card .ico{position:absolute;top:-34px;left:102px;width:88px;height:88px;border-radius:50%}
.card h3{margin-top:78px;font-size:21px}
.card p{margin:12px 20px 0;font-size:16.5px;line-height:34px;color:var(--muted)}
.card a{display:inline-block;margin-top:6px;color:#fff;font-size:16.5px;font-weight:600}
.protect{position:absolute;top:2037px;left:0;width:1200px;height:985px;background:var(--bg-deep)}
.side-title{position:absolute;font-size:32px}
.side-ghost{position:absolute;font-family:'Kanit',sans-serif;font-weight:600;color:var(--ghost);font-size:80px;line-height:1}
.side-text{position:absolute;font-size:16.5px;line-height:34px;color:var(--muted)}
.ticks{position:absolute;list-style:none;font-size:16.5px;line-height:35px;color:var(--muted)}
.ticks li{display:flex;align-items:center;gap:10px}
.contact{position:absolute;top:3022px;left:0;width:1200px;height:342px;background:var(--bg-panel)}
.subscribe{position:absolute;top:172px;left:200px;width:800px;height:74px;border-radius:37px;background:#fff;overflow:hidden}
.subscribe span{position:absolute;left:48px;top:24px;color:#4a3a45;font-size:18px}
.subscribe b{position:absolute;right:0;top:0;width:232px;height:74px;background:linear-gradient(90deg,var(--pink),var(--orange));
  font-family:'Kanit',sans-serif;font-weight:500;font-size:24px;color:#fff;text-align:center;line-height:74px;border-radius:0 37px 37px 0}
.footer{position:absolute;top:3364px;left:0;width:1200px;height:465px;background:var(--bg-footer)}
.footer .brand{top:100px;font-size:26px}
.f-about{position:absolute;top:152px;left:110px;width:250px;font-size:14px;line-height:26px;color:var(--muted)}
.socials{position:absolute;top:262px;left:110px;display:flex;gap:16px}
.socials span{width:29px;height:29px;background:var(--orange);border-radius:4px;display:block}
.f-col{position:absolute;top:100px}
.f-col h4{font-family:'Kanit',sans-serif;font-weight:400;font-size:21px;margin-bottom:12px}
.f-col ul{list-style:none;font-size:14.5px;line-height:40px;color:var(--muted)}
.f-col li{display:flex;align-items:center;gap:8px}
.f-contact li{line-height:22px;margin-bottom:16px;align-items:flex-start}
.f-rule{position:absolute;top:374px;left:110px;width:980px;height:1px;background:var(--line)}
.copy{position:absolute;top:404px;left:0;width:1200px;text-align:center;font-size:15px;color:var(--muted)}
</style>
</head>
<body>

<section class="hero">
  <div class="hero-art" role="img" aria-label="Hooded figure in shadow against a glowing pink binary code backdrop"></div>
  <h1>Welcome To<br>Domain Monitoring</h1>
  <p class="lead">Prevent Attacks By Monitoring Your Domains</p>
  <a class="btn">Get Started</a>
</section>

<header class="nav">
  <div class="brand">Domain Monitoring</div>
  <nav class="nav-links">
    <a class="active">Home</a><a>About</a><a>What Is Risk</a><a>Monitoring</a><a>How To Protect</a>
  </nav>
  <a class="btn">Contact Us</a>
</header>

<section class="about">
  <div class="ghost" style="top:103px">ABOUT US</div>
  <h2 class="sec-title" style="top:124px">Who We Are</h2>
  <p class="sec-text" style="top:193px;left:180px;width:840px">Vellora (company registration number CHE-481.902.117) was started in 2018 as a public limited company in Zug, Switzerland. Our analysts have long-standing relationships with various players on the Darknet.</p>
  <p class="sec-text" style="top:293px;left:190px;width:820px">These personal relationships make it possible for Vellora to repeatedly obtain the latest data leaks. Those unique data leaks are published by the press around the world.</p>
  <a class="btn" style="top:391px;left:530px">Read More</a>
</section>

<section class="risk">
  <div class="ghost" style="top:92px">DOMAIN MONITORING</div>
  <h2 class="sec-title" style="top:108px">What Is The Risk?</h2>
  <p class="sec-text" style="top:176px;left:150px;width:900px">Hackers use domain-based attacks, which are designed to trick users into submitting sensitive data or downloading dangerous files. This is often the case with phishing attacks. For example, domains can be registered that are very similar to one's own company, a customer or a supplier.</p>
  <p class="sec-text" style="top:310px;left:150px;width:900px">Once a fraudulent domain is registered, the hackers try to lure the employee to the website. This can be done via e-mail, SMS (smishing), instant messaging. Social media and many other techniques succeed. A distinction is made between different types of attacks:</p>
  <div class="card" style="left:112px">
    <div class="ico" role="img" aria-label="Email security icon" style="background:#3d5ce8"></div>
    <h3>Domain spoofing</h3>
    <p>Here, a domain name is registered that resembles that of a trusted brand or organization.</p>
    <a>Read More</a>
  </div>
  <div class="card" style="left:454px">
    <div class="ico" role="img" aria-label="Look-alike characters icon" style="background:linear-gradient(180deg,#ffb060,#ff8a3a)"></div>
    <h3>Homoglyphic attack</h3>
    <p>This is a variant of domain spoofing. Again, a similar looking domain is registered to.</p>
    <a>Read More</a>
  </div>
  <div class="card" style="left:797px">
    <div class="ico" role="img" aria-label="Misspelled web address icon" style="background:#ff0d6a"></div>
    <h3>Typosquatting</h3>
    <p>cybercriminals may attempt to register a malicious domain by using a common misspelling.</p>
    <a>Read More</a>
  </div>
</section>

<section class="protect">
  <div class="side-ghost" style="top:103px;left:110px">PROTECT</div>
  <h2 class="side-title" style="top:117px;left:110px">How To Protect Yourself?</h2>
  <p class="side-text" style="top:183px;left:111px;width:490px">Our domain monitoring solution continuously monitors thousands of TLDs, gTLDs and ccTLDs. For searches, we offer the greatest flexibility in the market and cover ALL forms of attacks.</p>
  <p class="side-text" style="top:320px;left:111px;width:490px">Here are a few examples of search options that can be adopted as active alerts:https://docs.vellora.example/search?id=domain_ database_search. All data can be analyzed and exported.</p>
  <div class="abs" role="img" aria-label="Yellow padlock in front of a computer monitor" style="top:126px;left:669px;width:320px;height:246px;border-radius:18px;background:linear-gradient(135deg,#2c2a2e 0%,#3a383c 45%,#e9a81a 46%,#ffc21a 100%)"></div>
  <div class="abs" role="img" aria-label="Shield with check mark beside a document and monitor" style="top:521px;left:164px;width:356px;height:334px;border-radius:18px;background:linear-gradient(135deg,#f2f2f2 0%,#c9d3dc 45%,#1e1e22 46%,#2b2b30 100%)"></div>
  <div class="side-ghost" style="top:525px;left:610px">MONITOR</div>
  <h2 class="side-title" style="top:542px;left:611px">What Else Are We Monitoring?</h2>
  <p class="side-text" style="top:608px;left:611px;width:500px">Vellora's alerting service can also detect threats before they turn into incidents. Vellora offers AI-driven dark web analysis, real-time threat alerts and pre-Attack threat indicators. Setup in minutes you will receive instant access to real-time reporting including:</p>
  <ul class="ticks" style="top:742px;left:611px">
    <li><svg width="17" height="14" viewBox="0 0 17 14"><path d="M1 7l5 5L16 1" fill="none" stroke="#ff9a4a" stroke-width="2.4"/></svg>People exposure: Social media monitoring</li>
    <li><svg width="17" height="14" viewBox="0 0 17 14"><path d="M1 7l5 5L16 1" fill="none" stroke="#ff9a4a" stroke-width="2.4"/></svg>Ransomware exposure: leak &amp; credential monitoring</li>
  </ul>
  <a class="btn" style="top:831px;left:613px">Read More</a>
</section>

<section class="contact">
  <div class="ghost" style="top:88px">CONTACT US</div>
  <h2 class="sec-title" style="top:89px">Get In Touch With Us</h2>
  <div class="subscribe"><span>Enter The Email</span><b>Subscribe</b></div>
</section>

<footer class="footer">
  <div class="brand">Domain Monitoring</div>
  <p class="f-about">Vellora (company registration number CHE-481.902.117) was started in 2018 as a public limited company in Zug, Switzerland.</p>
  <div class="socials"><span></span><span></span><span></span><span></span></div>
  <div class="f-col" style="left:419px">
    <h4>Quick Links</h4>
    <ul>
      <li><svg width="12" height="10" viewBox="0 0 12 10"><path d="M0 5h10M6 1l4 4-4 4" fill="none" stroke="#fff" stroke-width="1.5"/></svg>Home</li>
      <li><svg width="12" height="10" viewBox="0 0 12 10"><path d="M0 5h10M6 1l4 4-4 4" fill="none" stroke="#fff" stroke-width="1.5"/></svg>About</li>
      <li><svg width="12" height="10" viewBox="0 0 12 10"><path d="M0 5h10M6 1l4 4-4 4" fill="none" stroke="#fff" stroke-width="1.5"/></svg>What is Risk</li>
      <li><svg width="12" height="10" viewBox="0 0 12 10"><path d="M0 5h10M6 1l4 4-4 4" fill="none" stroke="#fff" stroke-width="1.5"/></svg>How to Protect</li>
      <li><svg width="12" height="10" viewBox="0 0 12 10"><path d="M0 5h10M6 1l4 4-4 4" fill="none" stroke="#fff" stroke-width="1.5"/></svg>Contact Us</li>
    </ul>
  </div>
  <div class="f-col" style="left:649px">
    <h4>Help Links</h4>
    <ul>
      <li><svg width="12" height="10" viewBox="0 0 12 10"><path d="M0 5h10M6 1l4 4-4 4" fill="none" stroke="#fff" stroke-width="1.5"/></svg>FAQ</li>
      <li><svg width="12" height="10" viewBox="0 0 12 10"><path d="M0 5h10M6 1l4 4-4 4" fill="none" stroke="#fff" stroke-width="1.5"/></svg>Terms</li>
      <li><svg width="12" height="10" viewBox="0 0 12 10"><path d="M0 5h10M6 1l4 4-4 4" fill="none" stroke="#fff" stroke-width="1.5"/></svg>Privacy Policy</li>
      <li><svg width="12" height="10" viewBox="0 0 12 10"><path d="M0 5h10M6 1l4 4-4 4" fill="none" stroke="#fff" stroke-width="1.5"/></svg>Support Links</li>
      <li><svg width="12" height="10" viewBox="0 0 12 10"><path d="M0 5h10M6 1l4 4-4 4" fill="none" stroke="#fff" stroke-width="1.5"/></svg>Conditions</li>
    </ul>
  </div>
  <div class="f-col f-contact" style="left:872px">
    <h4>Contact Us</h4>
    <ul>
      <li><svg width="14" height="16" viewBox="0 0 14 16"><path d="M7 1a5 5 0 0 1 5 5c0 4-5 9-5 9S2 10 2 6a5 5 0 0 1 5-5z" fill="none" stroke="#fff" stroke-width="1.4"/><circle cx="7" cy="6" r="1.8" fill="#fff"/></svg><span>Domain Monitoring<br>United States</span></li>
      <li><svg width="15" height="12" viewBox="0 0 15 12"><rect x="1" y="1" width="13" height="10" fill="none" stroke="#fff" stroke-width="1.3"/><path d="M1 1l6.5 5L14 1" fill="none" stroke="#fff" stroke-width="1.3"/></svg>hello@quillstonebrightmarsh.com</li>
      <li><svg width="14" height="14" viewBox="0 0 14 14"><path d="M3 1l2.5 3-1.5 1.5a8 8 0 0 0 4.5 4.5L10 8.5l3 2.5-1.5 2C6 13 1 8 1 2.5z" fill="none" stroke="#fff" stroke-width="1.3"/></svg>+1 555 014 2290</li>
    </ul>
  </div>
  <div class="f-rule"></div>
  <p class="copy">Copyrights@2022.Domain MonitoringAll Rights Reserved</p>
</footer>

</body>
</html>
```